Non Profit Company Looking For New Website

The website for Fernvale Quillstone Heritage Society should offer the viewer beautiful photos that inspire condifence and joy and tap into our love of horses.

We would like to see a website that displays trust, quality and confidence. Needs to be responsive and mobile friendly for all browsers and coded for both Android & IOS.

READ ATTACHED WEBSITE TEMPLATE FOR COMPLETE DETAILS ON WHAT WE ARE LOOKING FOR.

Looking for recommmendations if we should use WordPress/WooCommerce for site or Wordpress with Shopify Plug in or just Shopify.

Must be both desktop and mobile friendly with fast page load speed. Need the ability to edit ourselves.

Industry/Entity Type

Non Profit

Coding

Coded - Design and coding required

Number of Pages Required

5+ page

Requirements
Must have
• We would like to see a website that displays trust, quality and confidence. Needs to be responsive and mobile friendly for all browsers and coded for both Android & IOS.

Looking for recommendations if we should use WordPress/WooCommerce for site or Wordpress with Shopify Plug in or just Shopify.

Logo Colour:
Pantone 7621 C

READ TEMPLATE THAT IS ATTACHED
Nice to have
• Like look of this website as a sample:
https://www.quellbrimtorva.com/

Another similar non profit organization
https://pellaworthcindle.com/

```html
<!DOCTYPE html>
<html lang="en">
<head>
<meta charset="utf-8">
<title>Fernvale Quillstone Heritage Society — Website Layouts</title>
<link rel="stylesheet" href="https://fonts.googleapis.com/css2?family=Libre+Baskerville:wght@400;700&family=Lato:wght@400;700&display=swap">
<style>
:root{
  --red:#ab2328;
  --red-dark:#7e1a1f;
  --ink:#222;
  --muted:#777;
  --line:#e4d3d4;
  --blush:#fbf0f0;
  --board:#f4f2f2;
  --white:#fff;
  --serif:"Libre Baskerville",Georgia,serif;
  --sans:"Lato",Arial,sans-serif;
}
*{box-sizing:border-box;margin:0;padding:0}
html,body{width:1200px;height:3814px;overflow:hidden}
body{background:var(--board);font-family:var(--sans);color:var(--ink);position:relative}

.view-label{position:absolute;top:28px;font-family:var(--sans);font-size:13px;letter-spacing:7px;color:#333}
.view-label--desktop{left:400px}
.view-label--mobile{left:1010px}

.page{position:absolute;background:var(--white);box-shadow:0 4px 24px rgba(0,0,0,.12);overflow:hidden}
.page--desktop{left:20px;top:70px;width:870px;height:3700px}
.page--mobile{left:950px;top:70px;width:228px;height:3007px}
.page section,.page footer{position:relative}

.btn{display:inline-flex;align-items:center;justify-content:center;background:var(--red);color:var(--white);border-radius:20px;font-family:var(--sans);font-weight:700;white-space:nowrap}
.btn--light{background:var(--white);color:var(--red)}
.btn--outline{background:var(--white);color:var(--red);border:1.5px solid var(--red)}
.accent{color:var(--red)}
.dot{display:inline-block;border-radius:50%;background:var(--red)}
.photo{position:absolute}

.brand{font-family:var(--serif);color:var(--white);text-align:center;text-transform:uppercase;letter-spacing:2px;line-height:1.35}
.brand--footer{color:var(--red)}

/* ---------- Desktop ---------- */
.d-hero{height:545px;border-top:4px solid var(--red);background:linear-gradient(90deg,#3a2a24 0%,#5a3c2f 45%,#2f211c 100%)}
.d-hero .photo{inset:0;background:linear-gradient(180deg,rgba(0,0,0,.1),rgba(0,0,0,.35))}
.d-hero .brand{position:absolute;top:62px;left:0;right:0;font-size:12px}
.d-nav{position:absolute;top:193px;left:134px;width:602px;height:50px;background:rgba(30,25,25,.72);display:flex;justify-content:space-around;align-items:center;font-size:9px;color:var(--white)}
.d-nav .is-active{color:#e2474c}
.d-social{position:absolute;left:33px;top:236px;display:flex;flex-direction:column;gap:26px}
.d-social span{width:10px;height:10px;border-radius:50%;background:var(--white)}
.d-hero h1{position:absolute;top:285px;left:0;right:0;text-align:center;font-family:var(--serif);font-weight:400;font-size:31px;color:var(--white)}
.d-hero p{position:absolute;top:340px;left:0;right:0;text-align:center;font-size:9px;color:#eee;line-height:1.7}
.d-hero .btn{position:absolute;top:400px;left:365px;width:140px;height:27px;font-size:10px}

.d-callbar{position:absolute;top:512px;left:102px;width:666px;height:71px;background:var(--white);border:2px solid var(--red);border-top-width:1px;box-shadow:0 6px 10px rgba(0,0,0,.12);display:flex;align-items:center;padding:0 60px;gap:26px;font-size:9px;z-index:2}
.d-callbar .callbar-lead{font-weight:700;line-height:1.3;width:120px;border-right:1px solid #ccc}
.d-callbar .callbar-phone{display:flex;align-items:center;gap:14px;line-height:1.3}
.d-callbar .callbar-social{display:flex;gap:14px;margin-left:14px}
.d-callbar .dot{width:20px;height:20px}
.d-callbar .btn{width:78px;height:20px;font-size:8px;margin-left:14px}

.section-title{font-family:var(--serif);font-weight:700;text-align:center;color:var(--ink)}

.d-about{height:536px}
.d-about .section-title{position:absolute;top:128px;left:0;right:0;font-size:26px}
.d-about .about-copy{position:absolute;left:104px;top:240px;width:300px}
.d-about h3{font-family:var(--serif);font-size:24px;line-height:1.2;font-weight:700}
.d-about h3 small{font-size:18px;color:var(--ink)}
.d-about p{font-size:8.5px;line-height:1.8;color:var(--muted);margin-top:16px}
.d-about .btn{position:absolute;left:104px;top:465px;width:175px;height:28px;font-size:9px}
.d-about .photo{left:441px;top:227px;width:327px;height:261px;border:2px solid var(--line);background:linear-gradient(120deg,#6b4a34,#a88a6c 55%,#8f9a72)}

.d-donate{height:362px;background:linear-gradient(90deg,#6a3a25,#9a5a38 50%,#3d2218)}
.d-donate .panel{position:absolute;left:102px;top:67px;width:666px;height:224px;background:rgba(160,30,34,.82);text-align:center;color:var(--white)}
.d-donate h2{font-family:var(--serif);font-size:30px;font-weight:400;margin-top:44px}
.d-donate p{font-size:10px;line-height:1.7;margin:14px auto 0;width:460px}
.d-donate .btn{margin-top:18px;width:175px;height:28px;font-size:10px}

.d-adopt{height:1348px}
.d-adopt .section-title{position:absolute;top:95px;left:0;right:0;font-size:27px}
.d-adopt .intro{position:absolute;top:178px;left:0;right:0;text-align:center;font-size:9px;line-height:1.7;color:var(--muted)}
.horse-grid{position:absolute;top:240px;left:102px;width:666px;display:grid;grid-template-columns:326px 326px;gap:37px 14px}
.horse-card{border:1.5px solid #e8b7b9;background:var(--white);position:relative;height:463px;overflow:hidden}
.horse-card .photo{left:8px;right:8px;top:8px;height:205px;background:linear-gradient(180deg,#c9cfc2 0%,#8f8466 50%,#7a8c5a 100%)}
.horse-tag{position:absolute;top:8px;left:50%;transform:translateX(-50%);background:var(--red);color:var(--white);font-size:8px;font-weight:700;padding:4px 16px;z-index:1}
.horse-facts{position:absolute;left:22px;top:243px;font-size:9px;line-height:2.1;color:var(--ink)}
.horse-facts b{display:inline-block;width:66px}
.horse-facts .fee-note{color:var(--muted);font-size:8px;line-height:1.4;margin-bottom:8px}
.horse-facts span{color:var(--muted)}
.horse-actions{position:absolute;left:22px;right:22px;bottom:20px;display:flex;gap:10px}
.horse-actions .btn{height:20px;font-size:7.5px}
.horse-actions .btn:first-child{flex:1.6}
.horse-actions .btn:last-child{flex:1}
.d-adopt .cta-row{position:absolute;top:1273px;left:0;right:0;display:flex;justify-content:center;gap:14px}
.d-adopt .cta-row .btn{width:172px;height:28px;font-size:9px}

.d-contact{height:503px;background:var(--blush)}
.d-contact .photo{left:0;top:20px;width:326px;height:483px;background:linear-gradient(180deg,#f4e6e6 0%,#c98a8a 40%,#3a2620 80%,#1e1513)}
.contact-block{position:absolute;left:435px;top:60px;width:333px}
.contact-block h2{font-family:var(--serif);font-size:28px;font-weight:700}
.contact-block .intro{font-size:8.5px;line-height:1.7;color:var(--muted);margin-top:12px}
.field-grid{display:grid;grid-template-columns:1fr 1fr;gap:8px;margin-top:18px}
.field{height:28px;border:1px solid #ddd;background:var(--white);font-size:7.5px;color:#999;padding:8px}
.field--message{grid-column:1/3;height:100px}
.form-foot{display:flex;justify-content:space-between;align-items:center;margin-top:14px}
.captcha{width:130px;height:30px;border:1px solid #ddd;background:#f9f9f9;display:flex;align-items:center;gap:6px;padding:0 6px;font-size:6px;color:#555}
.captcha i{width:10px;height:10px;border:1px solid #999;background:var(--white)}
.form-foot .btn{width:162px;height:28px;border-radius:0;font-size:8px}
.info-row{display:grid;grid-template-columns:1fr 1fr 1fr;gap:8px;margin-top:28px}
.info-box{height:70px;border:1px solid #ddd;background:var(--white);text-align:center;font-size:6.5px;color:#777;padding-top:12px;line-height:1.4}
.info-box svg{display:block;margin:0 auto 6px}

.d-footer{height:406px;background:linear-gradient(180deg,#ede6e6,#f6f0f0)}
.d-footer .brand{position:absolute;top:75px;left:0;right:0;font-size:13px}
.footer-nav{display:flex;justify-content:center;gap:38px;background:var(--red);color:var(--white);font-size:9px;align-items:center}
.d-footer .footer-nav{position:absolute;top:207px;left:102px;width:666px;height:43px}
.footer-social{display:flex;justify-content:center;gap:24px}
.footer-social span{width:20px;height:20px;background:var(--red);border-radius:50%}
.d-footer .footer-social{position:absolute;top:283px;left:0;right:0}
.d-footer .copyright{position:absolute;top:383px;left:0;right:0;text-align:center;font-size:8px;color:#555}

/* ---------- Mobile ---------- */
.m-hero{height:315px;border-top:3px solid var(--red);background:linear-gradient(120deg,#3a2a24,#5c3d2f 55%,#2a1d18)}
.m-hero .brand{position:absolute;top:12px;left:0;right:0;font-size:6px;letter-spacing:1px}
.m-hero .m-topbar{position:absolute;top:80px;left:16px;right:16px;display:flex;align-items:center;gap:10px}
.m-hero .m-topbar span{width:7px;height:7px;border-radius:50%;background:var(--white)}
.m-hero .m-topbar svg{margin-left:auto}
.m-hero h1{position:absolute;top:140px;left:16px;right:10px;font-family:var(--serif);font-weight:400;font-size:13px;color:var(--white);white-space:nowrap}
.m-hero h1 .accent{color:#e2474c}
.m-hero p{position:absolute;top:168px;left:16px;right:16px;font-size:6px;line-height:1.5;color:#eee}
.m-hero .btn{position:absolute;top:228px;left:72px;width:84px;height:15px;font-size:6px}

.m-callcard{position:absolute;top:281px;left:20px;width:183px;height:203px;background:var(--white);border:1.5px solid var(--red);box-shadow:0 4px 8px rgba(0,0,0,.15);text-align:center;font-size:8px;z-index:2}
.m-callcard .lead{font-weight:700;line-height:1.4;margin-top:20px}
.m-callcard .phone{display:flex;align-items:center;justify-content:center;gap:20px;margin-top:22px;font-size:6.5px;line-height:1.4}
.m-callcard .icons{display:flex;justify-content:center;gap:10px;margin-top:20px}
.m-callcard .dot{width:16px;height:16px}
.m-callcard .btn{margin-top:20px;width:80px;height:16px;font-size:6px}

.m-about{height:708px}
.m-about .section-title{position:absolute;top:236px;left:0;right:0;font-size:15px}
.m-about .photo{left:10px;top:295px;width:208px;height:165px;border:1.5px solid var(--line);background:linear-gradient(120deg,#6b4a34,#a88a6c 55%,#8f9a72)}
.m-about h3{position:absolute;top:482px;left:30px;right:30px;text-align:center;font-family:var(--serif);font-size:12px;line-height:1.25}
.m-about h3 small{font-size:9px;color:var(--ink)}
.m-about p{position:absolute;top:528px;left:24px;right:24px;text-align:center;font-size:6px;line-height:1.6;color:var(--muted)}
.m-about .btn{position:absolute;top:659px;left:44px;width:140px;height:18px;font-size:6px}

.m-donate{height:237px;background:linear-gradient(90deg,#6a3a25,#9a5a38 50%,#3d2218)}
.m-donate .panel{position:absolute;left:26px;top:30px;width:176px;height:180px;background:rgba(160,30,34,.82);text-align:center;color:var(--white)}
.m-donate h2{font-family:var(--serif);font-size:14px;font-weight:400;margin-top:22px}
.m-donate p{font-size:7px;line-height:1.5;margin:10px 14px 0}
.m-donate .btn{margin-top:12px;width:110px;height:16px;font-size:6px}

.m-adopt{height:462px;overflow:hidden}
.m-adopt .section-title{position:absolute;top:66px;left:0;right:0;font-size:15px}
.m-adopt .horse-card{position:absolute;top:133px;left:8px;width:159px;height:309px;border-color:#e8b7b9}
.m-adopt .horse-card + .horse-card{left:183px}
.m-adopt .horse-card .photo{left:5px;right:5px;top:5px;height:100px}
.m-adopt .horse-tag{top:5px;font-size:5px;padding:2px 8px}
.m-adopt .horse-facts{left:10px;top:114px;font-size:6.5px;line-height:1.9}
.m-adopt .horse-facts b{width:42px}
.m-adopt .horse-facts .fee-note{font-size:5.5px;margin-bottom:3px}
.m-adopt .horse-stack{position:absolute;left:8px;right:8px;bottom:10px;display:flex;flex-direction:column;gap:5px}
.m-adopt .horse-stack .btn{height:13px;font-size:5.5px}

.m-contact{height:931px;background:var(--blush)}
.m-contact h2{position:absolute;top:58px;left:0;right:0;text-align:center;font-family:var(--serif);font-size:15px}
.m-contact .intro{position:absolute;top:88px;left:30px;right:30px;text-align:center;font-size:5.5px;line-height:1.5;color:var(--muted)}
.m-fields{position:absolute;top:130px;left:24px;right:24px;display:flex;flex-direction:column;gap:8px}
.m-fields .field{height:24px;font-size:5.5px;padding:7px;text-align:center}
.m-fields .field--message{height:96px}
.m-contact .captcha{position:absolute;top:368px;left:60px;width:108px;height:24px;font-size:5px}
.m-contact .btn{position:absolute;top:402px;left:56px;width:118px;height:22px;border-radius:0;font-size:6px}
.m-info{position:absolute;top:435px;left:60px;width:108px;display:flex;flex-direction:column;gap:8px}
.m-info .info-box{height:70px;font-size:5.5px}
.m-contact .photo{left:8px;top:681px;width:172px;height:248px;background:linear-gradient(180deg,#f4e6e6 0%,#c98a8a 35%,#3a2620 75%,#1e1513)}

.m-footer{height:354px;background:linear-gradient(180deg,#ede6e6,#f6f0f0)}
.m-footer .brand{position:absolute;top:32px;left:0;right:0;font-size:7px;letter-spacing:1px}
.m-footer .footer-nav{position:absolute;top:124px;left:8px;width:212px;height:77px;flex-wrap:wrap;gap:4px 18px;font-size:7px;padding:12px 20px}
.m-footer .footer-social{position:absolute;top:228px;left:0;right:0;gap:14px}
.m-footer .footer-social span{width:13px;height:13px}
.m-footer .copyright{position:absolute;top:290px;left:30px;right:30px;text-align:center;font-size:6.5px;line-height:1.6;color:#444}
</style>
</head>
<body>

<div class="view-label view-label--desktop">DESKTOP</div>
<div class="view-label view-label--mobile">MOBILE</div>

<main class="page page--desktop">
  <section class="d-hero">
    <div class="photo" role="img" aria-label="Photo of a bay thoroughbred wearing a bridle in a stable"></div>
    <div class="brand">Fernvale Quillstone<br>Heritage Society</div>
    <nav class="d-nav"><span class="is-active">Home</span><span>About</span><span>Adopt</span><span>Horses</span><span>Donate/Shop</span><span>Contact</span></nav>
    <div class="d-social"><span></span><span></span><span></span></div>
    <h1>Retire - <span class="accent">Retrain</span> - Rehome</h1>
    <p>We support and develop retired thoroughbred racehorses for their next chapter in life. Fernvale Quillstone Heritage<br>Society (FQHS) is a registered not-for-profit organization in Alberta.</p>
    <a class="btn">Contact us</a>
  </section>

  <div class="d-callbar">
    <div class="callbar-lead">Call to us for more<br>information</div>
    <div class="callbar-phone">
      <svg width="16" height="16" viewBox="0 0 24 24"><path d="M6.6 10.8a15 15 0 0 0 6.6 6.6l2.2-2.2a1 1 0 0 1 1-.25 11.4 11.4 0 0 0 3.6.57 1 1 0 0 1 1 1V20a1 1 0 0 1-1 1A17 17 0 0 1 3 4a1 1 0 0 1 1-1h3.5a1 1 0 0 1 1 1c0 1.25.2 2.45.57 3.57a1 1 0 0 1-.25 1z" fill="var(--red)"/></svg>
      <span>Call us now<br>555-014-2290</span>
    </div>
    <div class="callbar-social"><span class="dot"></span><span class="dot"></span><span class="dot"></span></div>
    <a class="btn">Contact us</a>
  </div>

  <section class="d-about">
    <h2 class="section-title">About us</h2>
    <div class="about-copy">
      <h3><small>What is </small><span class="accent">Thoroughbred Aftercare?</span></h3>
      <p>The health, safety and welfare of our equine athletes does not end at the finish line, and retirement and aftercare are critical to the success of the racing industry.</p>
      <p style="margin-top:8px">Aftercare is the safe placement of racehorses after their careers as racehorses are completed. Some horses might retire to the breeding shed or broodmare bands, while others are retrained for second careers.</p>
    </div>
    <a class="btn">Learn more about us</a>
    <div class="photo" role="img" aria-label="Photo of a girl gently touching noses with a chestnut horse"></div>
  </section>

  <section class="d-donate" role="img" aria-label="Background photo of horses with riders">
    <div class="panel">
      <h2>Donate now</h2>
      <p>Lorem Ipsum is simply dummy text of the printing and typesetting industry. Lorem Ipsum has been the industry's standard dummy text ever since the 1500s.</p>
      <a class="btn btn--light">Donate now</a>
    </div>
  </section>

  <section class="d-adopt">
    <h2 class="section-title">Adopt a horse</h2>
    <p class="intro">Fernvale Quillstone Heritage Society is committed to helping match you with the<br>perfect horse.</p>
    <div class="horse-grid">
      <article class="horse-card">
        <div class="horse-tag">THOROUGHBRED</div>
        <div class="photo" role="img" aria-label="Photo of a bay thoroughbred standing in a field"></div>
        <div class="horse-facts">
          <div><b>Fee :</b> $00.00</div>
          <div class="fee-note">Now – $00.00<br>Until – 5/31</div>
          <div><b>Birth year :</b> <span>2016</span></div>
          <div><b>Height :</b> <span>15.3</span></div>
          <div><b>Color :</b> <span>Bay</span></div>
          <div><b>Gender :</b> <span>Gelding</span></div>
          <div><b>Location :</b> <span>LEXINGTON, KY</span></div>
        </div>
        <div class="horse-actions"><a class="btn">View more about this horse</a><a class="btn">View all horses</a></div>
      </article>
      <article class="horse-card">
        <div class="horse-tag">THOROUGHBRED</div>
        <div class="photo" role="img" aria-label="Photo of a bay thoroughbred standing in a field"></div>
        <div class="horse-facts">
          <div><b>Fee :</b> $00.00</div>
          <div class="fee-note">Now – $00.00<br>Until – 5/31</div>
          <div><b>Birth year :</b> <span>2016</span></div>
          <div><b>Height :</b> <span>15.3</span></div>
          <div><b>Color :</b> <span>Bay</span></div>
          <div><b>Gender :</b> <span>Gelding</span></div>
          <div><b>Location :</b> <span>LEXINGTON, KY</span></div>
        </div>
        <div class="horse-actions"><a class="btn">View more about this horse</a><a class="btn">View all horses</a></div>
      </article>
      <article class="horse-card">
        <div class="horse-tag">THOROUGHBRED</div>
        <div class="photo" role="img" aria-label="Photo of a bay thoroughbred standing in a field"></div>
        <div class="horse-facts">
          <div><b>Fee :</b> $00.00</div>
          <div class="fee-note">Now – $00.00<br>Until – 5/31</div>
          <div><b>Birth year :</b> <span>2016</span></div>
          <div><b>Height :</b> <span>15.3</span></div>
          <div><b>Color :</b> <span>Bay</span></div>
          <div><b>Gender :</b> <span>Gelding</span></div>
          <div><b>Location :</b> <span>LEXINGTON, KY</span></div>
        </div>
        <div class="horse-actions"><a class="btn">View more about this horse</a><a class="btn">View all horses</a></div>
      </article>
      <article class="horse-card">
        <div class="horse-tag">THOROUGHBRED</div>
        <div class="photo" role="img" aria-label="Photo of a bay thoroughbred standing in a field"></div>
        <div class="horse-facts">
          <div><b>Fee :</b> $00.00</div>
          <div class="fee-note">Now – $00.00<br>Until – 5/31</div>
          <div><b>Birth year :</b> <span>2016</span></div>
          <div><b>Height :</b> <span>15.3</span></div>
          <div><b>Color :</b> <span>Bay</span></div>
          <div><b>Gender :</b> <span>Gelding</span></div>
          <div><b>Location :</b> <span>LEXINGTON, KY</span></div>
        </div>
        <div class="horse-actions"><a class="btn">View more about this horse</a><a class="btn">View all horses</a></div>
      </article>
    </div>
    <div class="cta-row"><a class="btn">Adopt now</a><a class="btn btn--outline">Donate now</a></div>
  </section>

  <section class="d-contact">
    <div class="photo" role="img" aria-label="Photo of a rider in a red jacket jumping a dark horse"></div>
    <div class="contact-block">
      <h2>Contact us</h2>
      <p class="intro">Have a question or need more information? Give us a call or the<br>form below.</p>
      <div class="field-grid">
        <div class="field">First name*</div><div class="field">Last name*</div>
        <div class="field">Your phone*</div><div class="field">Your email*</div>
        <div class="field field--message">Your message*</div>
      </div>
      <div class="form-foot">
        <div class="captcha"><i></i>I'm not a robot</div>
        <a class="btn">Submit your request</a>
      </div>
      <div class="info-row">
        <div class="info-box"><svg width="12" height="14" viewBox="0 0 24 28"><path d="M12 0a10 10 0 0 0-10 10c0 7.5 10 18 10 18s10-10.5 10-18A10 10 0 0 0 12 0zm0 14a4 4 0 1 1 0-8 4 4 0 0 1 0 8z" fill="var(--red)"/></svg>Lorem ipsum is simply<br>dummy text of the<br>printing</div>
        <div class="info-box"><svg width="12" height="12" viewBox="0 0 24 24"><path d="M6.6 10.8a15 15 0 0 0 6.6 6.6l2.2-2.2a1 1 0 0 1 1-.25 11.4 11.4 0 0 0 3.6.57 1 1 0 0 1 1 1V20a1 1 0 0 1-1 1A17 17 0 0 1 3 4a1 1 0 0 1 1-1h3.5a1 1 0 0 1 1 1c0 1.25.2 2.45.57 3.57a1 1 0 0 1-.25 1z" fill="var(--red)"/></svg>555-014-2290</div>
        <div class="info-box"><svg width="14" height="11" viewBox="0 0 24 18"><rect width="24" height="18" rx="2" fill="var(--red)"/><path d="M1 2l11 8 11-8" fill="none" stroke="#fff" stroke-width="2"/></svg>hello@fernvalequill.org</div>
      </div>
    </div>
  </section>

  <footer class="d-footer" role="contentinfo">
    <div class="brand brand--footer">Fernvale Quillstone<br>Heritage Society</div>
    <nav class="footer-nav"><span>Home</span><span>About</span><span>Adopt</span><span>Horses</span><span>Donate/Shop</span><span>Contact</span></nav>
    <div class="footer-social"><span></span><span></span><span></span></div>
    <p class="copyright">Copyright@2021-Fernvale Quillstone Heritage Society-Privacy Policy-Site Map</p>
  </footer>
</main>

<main class="page page--mobile">
  <section class="m-hero">
    <div class="brand">Fernvale Quillstone<br>Heritage Society</div>
    <div class="m-topbar"><span></span><span></span><span></span>
      <svg width="14" height="10" viewBox="0 0 14 10"><path d="M0 1h14M0 5h14M0 9h14" stroke="#fff" stroke-width="1.4"/></svg>
    </div>
    <h1>Retire - <span class="accent">Retrain</span> - Rehome</h1>
    <p>We support and develop retired thoroughbred racehorses for their next chapter in life. Fernvale Quillstone Heritage Society (FQHS) is a registered not-for-profit organization in Alberta.</p>
    <a class="btn">Contact us</a>
  </section>

  <div class="m-callcard">
    <p class="lead">Call to us for more<br>information</p>
    <div class="phone">
      <svg width="14" height="14" viewBox="0 0 24 24"><path d="M6.6 10.8a15 15 0 0 0 6.6 6.6l2.2-2.2a1 1 0 0 1 1-.25 11.4 11.4 0 0 0 3.6.57 1 1 0 0 1 1 1V20a1 1 0 0 1-1 1A17 17 0 0 1 3 4a1 1 0 0 1 1-1h3.5a1 1 0 0 1 1 1c0 1.25.2 2.45.57 3.57a1 1 0 0 1-.25 1z" fill="var(--red)"/></svg>
      <span>Call us now<br>555-014-2290</span>
    </div>
    <div class="icons"><span class="dot"></span><span class="dot"></span><span class="dot"></span></div>
    <a class="btn">Contact us</a>
  </div>

  <section class="m-about">
    <h2 class="section-title">About us</h2>
    <div class="photo" role="img" aria-label="Photo of a girl gently touching noses with a chestnut horse"></div>
    <h3><small>What is </small><span class="accent">Thoroughbred Aftercare?</span></h3>
    <p>The health, safety and welfare of our equine athletes does not end at the finish line, and retirement and aftercare are critical to the success of the racing industry.<br><br>Aftercare is the safe placement of racehorses after their careers as racehorses are completed. Some horses might retire to the breeding shed or broodmare bands, while others are retrained for second careers.</p>
    <a class="btn">Learn more about us</a>
  </section>

  <section class="m-donate" role="img" aria-label="Background photo of horses with riders">
    <div class="panel">
      <h2>Donate now</h2>
      <p>Lorem Ipsum is simply dummy text of the printing and typesetting industry. Lorem Ipsum has been the industry's standard dummy text ever since the 1500s.</p>
      <a class="btn btn--light">Donate now</a>
    </div>
  </section>

  <section class="m-adopt">
    <h2 class="section-title">Adopt a horse</h2>
    <article class="horse-card">
      <div class="horse-tag">THOROUGHBRED</div>
      <div class="photo" role="img" aria-label="Photo of a bay thoroughbred standing in a field"></div>
      <div class="horse-facts">
        <div><b>Fee :</b> $00.00</div>
        <div class="fee-note">Now – $00.00<br>Until – 5/31</div>
        <div><b>Birth year :</b> <span>2016</span></div>
        <div><b>Height :</b> <span>15.3</span></div>
        <div><b>Color :</b> <span>Bay</span></div>
        <div><b>Gender :</b> <span>Gelding</span></div>
        <div><b>Location :</b> <span>LEXINGTON, KY</span></div>
      </div>
      <div class="horse-stack"><a class="btn">View more about this horse</a><a class="btn">View all horses</a></div>
    </article>
    <article class="horse-card">
      <div class="horse-tag">THOROUGHBRED</div>
      <div class="photo" role="img" aria-label="Photo of a bay thoroughbred standing in a field"></div>
      <div class="horse-facts">
        <div><b>Fee :</b> $00.00</div>
        <div class="fee-note">Now – $00.00<br>Until – 5/31</div>
        <div><b>Birth year :</b> <span>2016</span></div>
        <div><b>Height :</b> <span>15.3</span></div>
        <div><b>Color :</b> <span>Bay</span></div>
        <div><b>Gender :</b> <span>Gelding</span></div>
        <div><b>Location :</b> <span>LEXINGTON, KY</span></div>
      </div>
      <div class="horse-stack"><a class="btn">View more about this horse</a><a class="btn">View all horses</a></div>
    </article>
  </section>

  <section class="m-contact">
    <h2>Contact us</h2>
    <p class="intro">Have a question or need more information? Give us a call or the form below.</p>
    <div class="m-fields">
      <div class="field">First name*</div>
      <div class="field">Last name*</div>
      <div class="field">Your phone*</div>
      <div class="field">Your email*</div>
      <div class="field field--message">Your message*</div>
    </div>
    <div class="captcha"><i></i>I'm not a robot</div>
    <a class="btn">Submit your request</a>
    <div class="m-info">
      <div class="info-box"><svg width="12" height="14" viewBox="0 0 24 28"><path d="M12 0a10 10 0 0 0-10 10c0 7.5 10 18 10 18s10-10.5 10-18A10 10 0 0 0 12 0zm0 14a4 4 0 1 1 0-8 4 4 0 0 1 0 8z" fill="var(--red)"/></svg>Lorem ipsum is simply<br>dummy text of the<br>printing</div>
      <div class="info-box"><svg width="12" height="12" viewBox="0 0 24 24"><path d="M6.6 10.8a15 15 0 0 0 6.6 6.6l2.2-2.2a1 1 0 0 1 1-.25 11.4 11.4 0 0 0 3.6.57 1 1 0 0 1 1 1V20a1 1 0 0 1-1 1A17 17 0 0 1 3 4a1 1 0 0 1 1-1h3.5a1 1 0 0 1 1 1c0 1.25.2 2.45.57 3.57a1 1 0 0 1-.25 1z" fill="var(--red)"/></svg>555-014-2290</div>
      <div class="info-box"><svg width="14" height="11" viewBox="0 0 24 18"><rect width="24" height="18" rx="2" fill="var(--red)"/><path d="M1 2l11 8 11-8" fill="none" stroke="#fff" stroke-width="2"/></svg>hello@fernvalequill.org</div>
    </div>
    <div class="photo" role="img" aria-label="Photo of a rider in a red jacket jumping a dark horse"></div>
  </section>

  <footer class="m-footer" role="contentinfo">
    <div class="brand brand--footer">Fernvale Quillstone<br>Heritage Society</div>
    <nav class="footer-nav"><span>Home</span><span>About</span><span>Adopt</span><span>Horses</span><span>Donate/Shop</span><span>Contact</span></nav>
    <div class="footer-social"><span></span><span></span><span></span></div>
    <p class="copyright">Copyright@2021-Fernvale Quillstone Heritage Society-Privacy Policy-Site Map</p>
  </footer>
</main>

</body>
</html>
```